Kelvor Engineers: Why you should hire us keepsake

New design. Open to plastic cards. We are an engineering firm that designs cell phone towers and commercial buildings. Please check out our website www.kelvorstruct.com for more details. We want people to remember our card and for it to be useful if possible. We want the same look and feel on these cards to be translated to other marketing material we may need such as brochures.

Target Market(s)

Architects, Developers and Telecommunication Carriers

Industry/Entity Type

Engineering

Contact Information for Business Card

Card with our company colors, logo, and innovative design with elements related to our industry.

Font styles to use
Sans Serif

Colors
9bcb3c
abd036
0255a3

Requirements
Must have
• Sleek and hip design
Nice to have
• Bright lime green and navy coloring that pops with an innovative design.
Should not have
• A basic and boring design

```html
<!DOCTYPE html>
<html lang="en">
<head>
<meta charset="utf-8">
<title>Kelvor Engineers Business Card</title>
<link href="https://fonts.googleapis.com/css2?family=Poppins:wght@400;500;600;800&display=swap" rel="stylesheet">
<style>
  :root {
    --navy: #1c3363;
    --lime: #cdd42a;
    --white: #ffffff;
    --page: #e9eaec;
  }
  * { margin: 0; padding: 0; box-sizing: border-box; }
  html, body { width: 1200px; height: 900px; overflow: hidden; background: var(--page); font-family: "Poppins", sans-serif; }
  .stage { position: relative; width: 1200px; height: 900px; }
  .card { position: absolute; left: 280px; width: 640px; height: 366px; border-radius: 22px; overflow: hidden; box-shadow: 0 6px 18px rgba(0,0,0,.18); }
  .card--back { top: 52px; background: var(--navy); }
  .card--front { top: 470px; background: var(--white); }

  .back-name { position: absolute; right: 70px; top: 100px; color: var(--lime); font-weight: 800; font-size: 56px; letter-spacing: -1px; line-height: 1.1; }
  .back-cities { position: absolute; left: 50px; top: 262px; color: var(--white); font-weight: 500; font-size: 17px; letter-spacing: 1.5px; white-space: nowrap; }
  .back-cities .sep { color: var(--lime); margin: 0 8px; }

  .front-name { position: absolute; left: 40px; top: 30px; color: var(--lime); font-weight: 800; font-size: 38px; letter-spacing: -0.5px; line-height: 1.2; }
  .rule { position: absolute; left: 40px; right: 40px; top: 172px; height: 2px; background: var(--navy); }
  .person { position: absolute; right: 48px; top: 108px; text-align: right; }
  .person-name { color: var(--navy); font-weight: 600; font-size: 22px; line-height: 1.2; }
  .person-title { color: var(--lime); font-weight: 400; font-size: 16px; line-height: 1.2; }
  .contacts { position: absolute; left: 40px; top: 186px; list-style: none; }
  .contacts li { display: flex; align-items: center; gap: 10px; color: var(--navy); font-size: 14px; line-height: 22px; }
  .contacts svg { width: 12px; height: 12px; flex: none; }
  .tagline { position: absolute; right: 60px; top: 280px; color: var(--navy); font-weight: 500; font-size: 16px; letter-spacing: 1px; line-height: 1.2; }
  .band { position: absolute; left: 0; bottom: 0; width: 640px; height: 60px; }
</style>
</head>
<body>
<div class="stage">
  <section class="card card--back">
    <div class="back-name">Kelvor Engineers</div>
    <div class="back-cities">DENVER<span class="sep">/</span>RALEIGH<span class="sep">/</span>PHOENIX<span class="sep">/</span>TULSA</div>
  </section>

  <section class="card card--front">
    <div class="front-name">Kelvor Engineers</div>
    <div class="person">
      <div class="person-name">Dana Ruth Halvorsen</div>
      <div class="person-title">Director</div>
    </div>
    <div class="rule"></div>
    <ul class="contacts">
      <li><svg viewBox="0 0 12 12"><path d="M2 1 L4 1 L5 3.5 L3.8 4.5 C4.5 6 6 7.5 7.5 8.2 L8.5 7 L11 8 L11 10 C11 10.6 10.6 11 10 11 C5 11 1 7 1 2 C1 1.4 1.4 1 2 1Z" fill="var(--lime)"/></svg>555.014.2231</li>
      <li><svg viewBox="0 0 12 12"><rect x="3" y="0.5" width="6" height="11" rx="1.2" fill="none" stroke="var(--lime)" stroke-width="1.2"/><circle cx="6" cy="9.5" r="0.7" fill="var(--lime)"/></svg>555.019.7740</li>
      <li><svg viewBox="0 0 12 12"><rect x="0.8" y="2.5" width="10.4" height="7" fill="none" stroke="var(--lime)" stroke-width="1.2"/><path d="M1 3 L6 7 L11 3" fill="none" stroke="var(--lime)" stroke-width="1.2"/></svg>dhalvorsen@kelvorstruct.com</li>
      <li><svg viewBox="0 0 12 12"><circle cx="6" cy="6" r="5" fill="none" stroke="var(--lime)" stroke-width="1.2"/><path d="M1 6 H11 M6 1 C3.5 4 3.5 8 6 11 M6 1 C8.5 4 8.5 8 6 11" fill="none" stroke="var(--lime)" stroke-width="1"/></svg>www.kelvorstruct.com</li>
    </ul>
    <div class="tagline">MULTI-DISCIPLINE ENGINEERING</div>
    <svg class="band" viewBox="0 0 640 60" preserveAspectRatio="none">
      <path d="M0 28 L300 28 C330 28 335 10 365 10 L640 10 L640 60 L0 60 Z" fill="var(--lime)"/>
      <path d="M0 36 L290 36 C320 36 330 16 360 16 L640 16 L640 60 L0 60 Z" fill="var(--white)"/>
      <path d="M0 41 L290 41 C322 41 332 20 362 20 L640 20 L640 60 L0 60 Z" fill="var(--navy)"/>
    </svg>
  </section>
</div>
</body>
</html>
```